Moon Tot needs ecommerce website design help

We need someone to set up a fully functional website for us. We sell baby bibs, I attached them along with our company logo (MTG: moon tot goods). The bibs are made of 100% silicon, they are safe, light weight, soft, smooth, flexible, dishwasher safe and has funny faces.

Business name: Moon Tot Goods
Elm Hollow, NY 00000
email: MoonTotGoods@mailbox-example.com
tel.: (555) 014-TOTS
website: MoonTotGoods-example.com

Target Market(s)

18-40

Industry/Entity Type

Baby

Coding

Coded - Design and coding required

Number of Pages Required

5+ page

Requirements
Must have
• 1. Pages: Why buy from us, Contact Us, Home page, Products Page, Blog
• 2. Use the colors from our logo for the web design.
• 3. Need a link that will connect visitors to our facebook, instagram, Pinterest and Tumblr account. Would like links on,the top left side of the page
Nice to have
• My Cart page
• 1. On contact us page, we want to include some type of template for the customer to complete. (Ex: name, email address, contact number, optional home address, comments)
• 2. When clients visit our website, we want a capture/pop up for the customer to subscribe to our email list to receive discounts. (Ex. Want 10% off your next order ? Suscribe to our mailing list below and get a 10% off code to use at check out. If they don't want to subscribe, they have the option to select "No Thank You, I want to pay full price).
• 3. On home page have subscribe to our email list.

```html
<!DOCTYPE html>
<html lang="en">
<head>
<meta charset="utf-8">
<title>Moon Tot Goods – Silicone Baby Bibs</title>
<link rel="stylesheet" href="https://fonts.googleapis.com/css2?family=Roboto:wght@300;400;500;700&family=Oswald:wght@400;500&display=swap">
<style>
:root{
  --orange:#fbb55c;
  --pink:#f0506e;
  --green:#8dc63f;
  --blue:#2a9fe0;
  --yellow:#f5e21c;
  --ink:#222;
  --muted:#666;
  --dark:#4a4848;
  --footer:#1b1b1b;
  --light:#f1f1f1;
}
*{box-sizing:border-box;margin:0;padding:0}
html,body{width:1200px;height:2320px;overflow:hidden}
body{font-family:"Roboto",sans-serif;color:var(--ink);background:#fff;position:relative}
a{color:inherit;text-decoration:none}

/* top bar */
.topbar{position:absolute;left:0;top:0;width:1200px;height:28px;background:var(--orange);font-size:9px;font-weight:500;color:#3a2a10;letter-spacing:.3px}
.topbar .follow{position:absolute;left:608px;top:9px}
.topbar .social{position:absolute;left:695px;top:8px;display:flex;gap:11px}
.topbar .social span{width:9px;height:11px;background:#3a2a10;border-radius:2px}
.topbar .links{position:absolute;left:818px;top:9px;display:flex;gap:26px}
.topbar .phone{display:flex;align-items:center;gap:4px;font-size:10px}

/* header */
.brand{position:absolute;display:flex;align-items:center;gap:12px}
.brand .dot{width:46px;height:46px;border-radius:50%;background:var(--orange)}
.brand .name{font-family:"Roboto",sans-serif;font-weight:700;font-size:46px;color:var(--pink);letter-spacing:2px}
.search{position:absolute;left:603px;top:48px;width:237px;height:34px;border:1px solid #cfcfcf;display:flex;align-items:center;padding-left:12px;gap:8px;font-size:9px;color:#555;letter-spacing:.5px}
.cart{position:absolute;left:935px;top:48px;width:132px;height:32px;background:var(--green);display:flex;align-items:center;padding-left:8px;gap:10px;font-size:10px;color:#1d3a05;font-weight:500}
.cart .badge{position:absolute;left:22px;top:3px;width:12px;height:12px;border-radius:50%;background:var(--pink);color:#fff;font-size:8px;text-align:center;line-height:12px}
.nav{position:absolute;left:603px;top:100px;display:flex;font-size:11px;font-weight:500;letter-spacing:.3px}
.nav a{height:28px;line-height:28px;padding:0 12px;margin-right:22px;color:#222}
.nav a.active{background:var(--pink);color:#fff}

/* hero */
.hero{position:absolute;left:0;top:139px;width:1200px;height:476px;background:linear-gradient(90deg,#f2f2f2,#e4e4e4)}
.hero h1{position:absolute;left:133px;top:104px;font-weight:300;font-size:44px;line-height:52px;color:#1c1c1c}
.hero h1 strong{display:block;font-weight:700;color:var(--pink)}
.hero p{position:absolute;left:133px;top:222px;width:370px;font-size:16px;line-height:28px;color:#333}
.btn-learn{position:absolute;left:133px;top:297px;width:150px;height:46px;background:var(--orange);color:#2a1a05;font-size:14px;font-weight:500;text-align:center;line-height:46px;letter-spacing:.5px}
.hero-art{position:absolute;left:603px;top:16px;width:464px;height:432px;border-radius:40px;background:radial-gradient(circle at 32% 60%,#2a9fe0 0 30%,transparent 31%),radial-gradient(circle at 68% 48%,#e9229a 0 34%,transparent 35%)}
.dots{position:absolute;left:556px;top:436px;display:flex;gap:12px;align-items:center}
.dots i{width:7px;height:7px;border-radius:50%;background:#333}
.dots i.on{width:11px;height:11px;background:none;border:1.5px solid #333}

/* section title */
.sec-title{position:absolute;left:0;width:1200px;text-align:center;font-size:21px;font-weight:500;color:var(--pink);letter-spacing:.5px}
.sec-title::after{content:"";display:block;width:222px;height:2px;background:var(--orange);margin:9px auto 0}

/* products */
.card{position:absolute;top:716px;width:226px;height:306px;background:#fff;box-shadow:0 2px 8px rgba(0,0,0,.2);text-align:center}
.card .fav{position:absolute;right:8px;top:0;width:22px;height:22px;background:var(--pink);display:flex;align-items:center;justify-content:center}
.card .art{width:140px;height:140px;margin:30px auto 0;border-radius:50% 50% 45% 45%}
.card h3{font-size:12px;font-weight:400;margin-top:26px;color:#111}
.card .price{font-family:"Oswald",sans-serif;font-size:24px;color:var(--pink);margin-top:10px}
.card .add{display:inline-flex;align-items:center;gap:6px;margin-top:10px;height:24px;padding:0 9px;background:var(--orange);font-size:8px;font-weight:500;color:#2a1a05}
.arrow{position:absolute;top:840px;width:32px;height:37px;background:#2b2b2b;display:flex;align-items:center;justify-content:center}

/* why */
.why{position:absolute;left:0;top:1068px;width:1200px;height:478px;background:var(--dark);color:#fff}
.why h2{position:absolute;left:130px;top:40px;font-size:20px;font-weight:500}
.why .lead{position:absolute;left:130px;top:78px;width:525px;font-size:11px;line-height:19px;color:#eee}
.feat{position:absolute;left:130px;width:560px;height:72px}
.feat .ico{position:absolute;left:0;top:0;width:72px;height:72px;border-radius:50%;display:flex;align-items:center;justify-content:center}
.feat h4{position:absolute;left:94px;top:4px;font-size:13px;font-weight:500}
.feat p{position:absolute;left:94px;top:24px;width:410px;font-size:9.5px;line-height:18px;color:#ddd}
.feat p.narrow{width:360px}
.promo{position:absolute;left:705px;width:362px;height:187px;overflow:hidden}
.promo.sale{top:42px;background:#b88a3a}
.promo.sale .photo{position:absolute;left:170px;top:0;width:192px;height:187px;background:linear-gradient(135deg,#d9a25a,#8a5a3a)}
.promo.sale .t1{position:absolute;left:22px;top:14px;font-size:30px;font-weight:300}
.promo.sale .t2{position:absolute;left:22px;top:48px;font-size:28px;font-weight:700}
.promo.sale .t3{position:absolute;left:22px;top:86px;font-size:38px;font-weight:700}
.promo.sale .t3 small{font-size:24px}
.promo.sale .buy{position:absolute;left:24px;top:136px;width:92px;height:28px;background:var(--green);color:#1d3a05;font-size:12px;font-weight:500;text-align:center;line-height:28px}
.promo.new{top:255px;background:linear-gradient(180deg,#c9c9c9,#9ea3ab);color:#111;text-align:center}
.promo.new .rack{position:absolute;left:0;bottom:0;width:362px;height:96px;background:linear-gradient(90deg,#e8e0d6,#c94a4a 30%,#e8e0d6 50%,#7aa0c8 75%,#e8e0d6)}
.promo.new h3{position:relative;margin-top:10px;font-size:23px;font-weight:700;color:#222}
.promo.new p{position:relative;width:230px;margin:6px auto 0;font-size:11px;line-height:16px}
.promo.new .buy{position:absolute;left:136px;top:136px;width:92px;height:32px;background:var(--pink);color:#fff;font-size:12px;font-weight:500;line-height:32px}

/* blog */
.blog{position:absolute;left:0;top:1546px;width:1200px;height:471px;background:var(--light)}
.post{position:absolute;top:104px;width:298px;height:320px;background:#fff;box-shadow:0 1px 4px rgba(0,0,0,.12)}
.post .img{height:168px;position:relative}
.post .date{position:absolute;left:12px;top:0;width:36px;height:52px;background:var(--pink);color:#fff;text-align:center}
.post .date b{display:block;font-family:"Oswald",sans-serif;font-weight:400;font-size:20px;line-height:30px}
.post .date span{font-size:9px}
.post h3{margin:20px 48px 0 20px;font-size:12.5px;font-weight:500;line-height:17px;color:#111}
.post p{margin:10px 20px 0;font-size:11px;line-height:18px;color:#555;text-align:justify}
.post .more{position:absolute;left:20px;top:274px;height:24px;padding:0 10px;background:var(--orange);font-size:9px;font-weight:500;line-height:24px;color:#2a1a05}

/* footer */
.footer{position:absolute;left:0;top:2017px;width:1200px;height:303px;background:var(--footer);color:#fff}
.footer h5{position:absolute;top:52px;font-size:11px;font-weight:700;letter-spacing:.3px}
.footer ul{position:absolute;top:76px;list-style:none;font-size:10px;line-height:17.5px;color:#eee}
.footer .email{position:absolute;left:768px;top:81px;width:300px;height:39px;border:1px solid #555;background:#2a2a2a;display:flex;align-items:center;padding-left:14px;gap:12px;font-size:11px;color:#ccc}
.footer .signup{position:absolute;left:768px;top:135px;width:300px;height:40px;background:var(--pink);font-size:17px;font-weight:700;text-align:center;line-height:40px}
.footer hr{position:absolute;left:130px;top:220px;width:938px;border:0;border-top:1px solid #3a3a3a}
.footer .follow{position:absolute;left:132px;top:257px;font-size:9px;font-weight:700}
.footer .social{position:absolute;left:232px;top:250px;display:flex;gap:9px}
.footer .social span{width:26px;height:26px;border-radius:50%}
.footer .copy{position:absolute;right:132px;top:258px;font-size:9px;color:#ddd}
</style>
</head>
<body>

<header>
  <div class="topbar">
    <span class="follow">FOLLOW US ON :</span>
    <div class="social" aria-label="Social links"><span></span><span></span><span></span><span></span></div>
    <div class="links">
      <a>LOGIN</a><a>MY ACCOUNT</a>
      <span class="phone"><svg width="9" height="9" viewBox="0 0 10 10"><path d="M2 1l2 2-1 1.5c.6 1.2 1.3 1.9 2.5 2.5L7 6l2 2-1.5 1.5C4.5 9 1 5.5.5 2.5z" fill="#3a2a10"/></svg>(555) 014-TOTS</span>
    </div>
  </div>

  <a class="brand" style="left:130px;top:58px"><span class="dot"></span><span class="name">MTG</span></a>

  <div class="search"><svg width="10" height="10" viewBox="0 0 10 10"><circle cx="4" cy="4" r="3" fill="none" stroke="#333" stroke-width="1.4"/><path d="M6.3 6.3L9 9" stroke="#333" stroke-width="1.4"/></svg>SEARCH</div>
  <div class="cart"><svg width="16" height="14" viewBox="0 0 16 14"><path d="M0 1h3l2 8h8l2-6H4" fill="none" stroke="#1d3a05" stroke-width="1.6"/><circle cx="6" cy="12" r="1.3" fill="#1d3a05"/><circle cx="12" cy="12" r="1.3" fill="#1d3a05"/></svg><span class="badge">0</span>MY CART &nbsp;$0.00</div>

  <nav class="nav"><a class="active">HOME</a><a>PRODUCTS</a><a>WHY BUY FROM US</a><a>BLOG</a><a>CONTACT US</a></nav>
</header>

<section class="hero">
  <h1>The bibs are made of<strong>100% silicon</strong></h1>
  <p>safe, light weight, soft, smooth, flexible, dishwasher safe and has funny faces</p>
  <a class="btn-learn">LEARN MORE</a>
  <div class="hero-art" role="img" aria-label="Blue and pink silicone bibs with funny faces"></div>
  <div class="dots"><i></i><i class="on"></i><i></i><i></i><i></i></div>
</section>

<h2 class="sec-title" style="top:646px">FEATURED PRODUCTS</h2>

<a class="arrow" style="left:96px"><svg width="8" height="12" viewBox="0 0 8 12"><path d="M6 1L1 6l5 5" fill="none" stroke="#fff" stroke-width="2"/></svg></a>
<a class="arrow" style="left:1070px"><svg width="8" height="12" viewBox="0 0 8 12"><path d="M2 1l5 5-5 5" fill="none" stroke="#fff" stroke-width="2"/></svg></a>

<div class="card" style="left:130px"><span class="fav"><svg width="12" height="11" viewBox="0 0 12 11"><path d="M6 10L1.2 5.3A2.8 2.8 0 016 1.8a2.8 2.8 0 014.8 3.5z" fill="none" stroke="#fff" stroke-width="1.3"/></svg></span><div class="art" role="img" aria-label="Green silicone bib" style="background:radial-gradient(circle,#8dc63f 60%,#fff 62%)"></div><h3>Lorem Ipsum is simply dummy</h3><div class="price">$7.99</div><a class="add"><svg width="9" height="8" viewBox="0 0 16 14"><path d="M0 1h3l2 8h8l2-6H4" fill="none" stroke="#000" stroke-width="2"/></svg>ADD TO CART</a></div>
<div class="card" style="left:368px"><span class="fav"><svg width="12" height="11" viewBox="0 0 12 11"><path d="M6 10L1.2 5.3A2.8 2.8 0 016 1.8a2.8 2.8 0 014.8 3.5z" fill="none" stroke="#fff" stroke-width="1.3"/></svg></span><div class="art" role="img" aria-label="Orange silicone bib" style="background:radial-gradient(circle,#f7941d 55%,#fff 57%)"></div><h3>It is a long established</h3><div class="price">$8.99</div><a class="add"><svg width="9" height="8" viewBox="0 0 16 14"><path d="M0 1h3l2 8h8l2-6H4" fill="none" stroke="#000" stroke-width="2"/></svg>ADD TO CART</a></div>
<div class="card" style="left:604px"><span class="fav"><svg width="12" height="11" viewBox="0 0 12 11"><path d="M6 10L1.2 5.3A2.8 2.8 0 016 1.8a2.8 2.8 0 014.8 3.5z" fill="none" stroke="#fff" stroke-width="1.3"/></svg></span><div class="art" role="img" aria-label="Blue silicone bib" style="background:radial-gradient(circle,#2a9fe0 60%,#fff 62%)"></div><h3>There are many variations</h3><div class="price">$10.99</div><a class="add"><svg width="9" height="8" viewBox="0 0 16 14"><path d="M0 1h3l2 8h8l2-6H4" fill="none" stroke="#000" stroke-width="2"/></svg>ADD TO CART</a></div>
<div class="card" style="left:843px"><span class="fav"><svg width="12" height="11" viewBox="0 0 12 11"><path d="M6 10L1.2 5.3A2.8 2.8 0 016 1.8a2.8 2.8 0 014.8 3.5z" fill="none" stroke="#fff" stroke-width="1.3"/></svg></span><div class="art" role="img" aria-label="Yellow silicone bib" style="background:radial-gradient(circle,#f5e21c 58%,#fff 60%)"></div><h3>The standard chunk of Lorem</h3><div class="price">$12.99</div><a class="add"><svg width="9" height="8" viewBox="0 0 16 14"><path d="M0 1h3l2 8h8l2-6H4" fill="none" stroke="#000" stroke-width="2"/></svg>ADD TO CART</a></div>

<section class="why">
  <h2>WHY BUY FROM US</h2>
  <p class="lead">Contrary to popular belief, Lorem Ipsum is not simply random text. It has roots in a piece of classical Latin literature from 45 BC, making it over 2000 years old.</p>

  <div class="feat" style="top:145px">
    <span class="ico" style="background:var(--green)"><svg width="30" height="30" viewBox="0 0 30 30"><path d="M4 13h5v13H4zM11 13l5-9c2 0 3 1 2.5 3.5L17.5 12H25c1.5 0 2.5 1.3 2 2.8l-2.5 9c-.4 1.3-1.4 2.2-2.7 2.2H11z" fill="#fff"/></svg></span>
    <h4 style="color:var(--green)">QUALITY</h4>
    <p class="narrow">It has roots in a piece of classical Latin literature from 45 BC, making it over 2000 years old.</p>
  </div>
  <div class="feat" style="top:255px">
    <span class="ico" style="background:var(--pink)"><svg width="30" height="30" viewBox="0 0 30 30"><circle cx="15" cy="12" r="8" fill="none" stroke="#fff" stroke-width="2.4"/><circle cx="15" cy="12" r="3.5" fill="#fff"/><path d="M10 18l-3 9 4-2 2 3 2-8M20 18l3 9-4-2-2 3-2-8" fill="#fff"/></svg></span>
    <h4 style="color:var(--pink)">BEST SERVICES</h4>
    <p>Contrary to popular belief, Lorem Ipsum is not simply random text. It has roots in a piece of classical Latin literature from 45 BC, making it over.</p>
  </div>
  <div class="feat" style="top:366px">
    <span class="ico" style="background:var(--orange)"><svg width="36" height="26" viewBox="0 0 36 26"><path d="M2 4h20v14H2zM22 9h7l5 5v4H22z" fill="#fff"/><circle cx="9" cy="20" r="3.2" fill="#fff" stroke="#fbb55c" stroke-width="1.5"/><circle cx="27" cy="20" r="3.2" fill="#fff" stroke="#fbb55c" stroke-width="1.5"/></svg></span>
    <h4 style="color:var(--orange)">FREE DELIVERY</h4>
    <p>Contrary to popular belief, Lorem Ipsum is not simply random text. It has roots in a piece of classical Latin literature from 45 BC, making it over.</p>
  </div>

  <div class="promo sale">
    <div class="photo" role="img" aria-label="Smiling baby wearing a blue silicone bib"></div>
    <div class="t1">Buy</div>
    <div class="t2">BABY BIBS</div>
    <div class="t3">10% <small>OFF</small></div>
    <a class="buy">BUY NOW</a>
  </div>
  <div class="promo new">
    <div class="rack" role="img" aria-label="Row of colourful cloth bibs hanging on a line"></div>
    <h3>WHATS NEW</h3>
    <p>There are many variations of passages of Lorem Ipsum available</p>
    <a class="buy">BUY NOW</a>
  </div>
</section>

<section class="blog">
  <h2 class="sec-title" style="top:34px">OUR BLOG</h2>

  <article class="post" style="left:130px">
    <div class="img" role="img" aria-label="Toddler in a bib sitting at a table" style="background:linear-gradient(135deg,#bcd6ea,#e9dcc8 55%,#8ab4d8)"><span class="date"><b>20</b><span>JAN</span></span></div>
    <h3>Lorem Ipsum is simply dummy text of the printing</h3>
    <p>There are many variations of passages of Lorem Ipsum available, but the.</p>
    <a class="more">READ MORE</a>
  </article>
  <article class="post" style="left:450px">
    <div class="img" role="img" aria-label="Baby wearing a white bib" style="background:linear-gradient(135deg,#f3f3f3,#efe2d4 55%,#f6f6f6)"><span class="date"><b>22</b><span>JAN</span></span></div>
    <h3>It is a long established fact that a reader will be distracted</h3>
    <p>The standard chunk of Lorem Ipsum used since the 1500s is reproduced below for.</p>
    <a class="more">READ MORE</a>
  </article>
  <article class="post" style="left:770px">
    <div class="img" role="img" aria-label="Cloth bib with yellow trim" style="background:linear-gradient(135deg,#fafafa,#ece8e2 60%,#f7f7f7)"><span class="date"><b>18</b><span>JAN</span></span></div>
    <h3>There are many variations of passages of Lorem Ipsum</h3>
    <p>Various versions have evolved over the years, sometimes by accident.</p>
    <a class="more">READ MORE</a>
  </article>
</section>

<footer class="footer">
  <a class="brand" style="left:130px;top:62px"><span class="dot"></span><span class="name">MTG</span></a>

  <h5 style="left:379px">MENU</h5>
  <ul style="left:381px"><li>Home</li><li>Product</li><li>Why buy from us</li><li>Blog</li><li>Contact us</li></ul>

  <h5 style="left:549px">CONTACT US</h5>
  <ul style="left:551px"><li>Moon Tot Goods</li><li>Elm Hollow, NY 00000</li><li>Email: MoonTotGoods@mailbox-example.com</li><li>Tel.: (555) 014-TOTS</li></ul>

  <h5 style="left:768px">NEWSLETTER SUBSCRIBE</h5>
  <div class="email"><svg width="12" height="9" viewBox="0 0 12 9"><rect width="12" height="9" fill="#ccc"/><path d="M0 0l6 5 6-5" fill="none" stroke="#2a2a2a" stroke-width="1.2"/></svg>E mail id</div>
  <a class="signup">SIGNUP!</a>

  <hr>
  <span class="follow">FOLLOW US ON :</span>
  <div class="social" aria-label="Social links"><span style="background:#5a6fb0"></span><span style="background:#2a9fe0"></span><span style="background:#e5574a"></span><span style="background:#7a7a7a"></span></div>
  <span class="copy">Copyrights @ 2016 All Rights Reserved</span>
</footer>

</body>
</html>
```